New Business Cards for Tormin Group

We need a new Business Card to compliment our new logo. We are a vibrant design, manufacture and install business providing recreation areas, public parks and Municipal spaces. We want business cards that are classy, modern and clean.

We have recently changed our logo, and are celebrating our 40th anniversary. We want business cards with a new modern design to reflect our status.

Target Market(s)

Customers

Contact Information for Business Card

We need all the details of our 3 offices as per the business card attached. Please disregard the old logo on the business card, the other three files show our new logo.

Requirements
Must have
• All info as per attached business card but with new logo.
Nice to have

```html
<!DOCTYPE html>
<html lang="en">
<head>
<meta charset="utf-8">
<title>Tormin Group – Business Card</title>
<link rel="stylesheet" href="https://fonts.googleapis.com/css2?family=Lato:wght@400;700;900&display=swap">
<style>
  :root {
    --bg: #5e5e5e;
    --card: #ffffff;
    --red: #e8313a;
    --ink: #3a3a3a;
    --text: #555555;
    --rule: #6a6a6a;
    --band: #4a4a4a;
  }
  * { margin: 0; padding: 0; box-sizing: border-box; }
  html, body {
    width: 1200px; height: 1200px; overflow: hidden;
    background: var(--bg);
    font-family: "Lato", sans-serif;
  }
  .card {
    position: absolute; left: 139px; top: 370px;
    width: 922px; height: 537px;
    background: var(--card);
    border-radius: 36px;
    overflow: hidden;
  }
  .card > * { position: absolute; }
  .name { left: 31px; top: 86px; font-size: 34px; font-weight: 400; color: var(--red); }
  .role { left: 31px; top: 138px; font-size: 21px; color: var(--ink); }
  .brand { right: 26px; top: 54px; display: flex; align-items: center; gap: 14px; }
  .brand-mark { width: 108px; height: 108px; border-radius: 50%; background: var(--red); }
  .brand-name { font-size: 30px; font-weight: 900; color: var(--ink); letter-spacing: 0.5px; }
  .contact { left: 31px; top: 253px; font-size: 17px; color: var(--text); line-height: 32px; }
  .contact .label { color: var(--red); }
  .website { left: 657px; top: 285px; font-size: 17px; color: var(--text); line-height: 32px; }
  .rule { left: 31px; top: 324px; width: 864px; height: 2px; background: var(--rule); }
  .office { top: 346px; color: var(--text); font-size: 17px; line-height: 28px; }
  .office h2 { font-size: 22px; font-weight: 400; color: var(--red); margin-bottom: 6px; line-height: 30px; }
  .office--head { left: 31px; }
  .office--dubai { left: 354px; }
  .office--qatar { left: 657px; top: 350px; }
  .band { left: 0; bottom: 0; width: 100%; height: 30px; background: var(--band); }
  .band-accent {
    bottom: 0; left: 292px; width: 343px; height: 30px;
    background: var(--red);
    border-left: 7px solid var(--card); border-right: 7px solid var(--card);
  }
</style>
</head>
<body>
  <div class="card">
    <div class="name">Marc Haddad</div>
    <div class="role">Managing Partner</div>

    <div class="brand">
      <div class="brand-mark"></div>
      <div class="brand-name">TORMIN GROUP</div>
    </div>

    <div class="contact">
      <div><span class="label">Phone:</span> +971 (0)50 318 4702</div>
      <div><span class="label">Email:</span> marc@tormingroup.com</div>
    </div>
    <div class="website">www.tormingroup.com</div>

    <div class="rule"></div>

    <section class="office office--head">
      <h2>Head Office</h2>
      <p>P.O. Box: 41820 Abu Dhabi. U.A.E</p>
      <p>Tel No: +971 (0)2 5117302</p>
      <p>Fax No: +971(0)2 5117303</p>
      <p>Email: sales@tormingroup.com</p>
    </section>
    <section class="office office--dubai">
      <h2>Dubai Office</h2>
      <p>P.O. Box: 528144 Dubai, U.A.E</p>
      <p>Tel No: +971 (0)4 367240</p>
      <p>Fax No: +971(0)4 367288</p>
      <p>Email: sales@tormingroup.com</p>
    </section>
    <section class="office office--qatar">
      <h2>Qatar Office</h2>
      <p>P.O. Box: 20937 Doha, Qatar</p>
      <p>Tel No: +974 44719853</p>
      <p>Fax No: +974 44719860</p>
      <p>Email: sales@tormingroup.com</p>
    </section>

    <div class="band"></div>
    <div class="band-accent"></div>
  </div>
</body>
</html>
```